Business card design for my company.
I would like the card's background colour to be black. You can also see our web site to get an idea of our brand. https://www.tmwhomecrafting.com.au/
- Name
- Email

```html
<!DOCTYPE html>
<html lang="en">
<head>
<meta charset="utf-8">
<title>TMW Home Crafting – Business Card</title>
<link rel="stylesheet" href="https://fonts.googleapis.com/css2?family=Montserrat:wght@400;500;700&display=swap">
<style>
  :root {
    --backdrop: #2b2b2b;
    --card-black: #141414;
    --brand-green: #1f9a45;
    --green-light: #27a84f;
    --green-dark: #15803a;
    --ink-white: #f2f2f2;
    --shadow: rgba(0, 0, 0, 0.55);
  }
  * { box-sizing: border-box; margin: 0; padding: 0; }
  html, body {
    width: 1200px;
    height: 689px;
    overflow: hidden;
    background: var(--backdrop);
    font-family: "Montserrat", Arial, sans-serif;
  }
  .canvas {
    position: relative;
    width: 1200px;
    height: 689px;
    display: flex;
    align-items: center;
    justify-content: center;
    gap: 50px;
  }
  .card {
    position: relative;
    width: 530px;
    height: 303px;
    border-radius: 22px;
    overflow: hidden;
    box-shadow: 0 18px 40px var(--shadow);
  }
  /* Back side */
  .card-back__pattern {
    position: absolute;
    inset: 0;
    background: linear-gradient(120deg, var(--green-light) 0%, var(--brand-green) 55%, var(--green-dark) 100%);
  }
  /* Front side */
  .card-front {
    background: var(--card-black);
  }
  .brand {
    position: absolute;
    left: 48px;
    top: 150px;
    display: flex;
    align-items: center;
    gap: 12px;
  }
  .brand__mark {
    width: 18px;
    height: 18px;
    background: var(--brand-green);
  }
  .brand__name {
    color: var(--ink-white);
    font-weight: 700;
    font-size: 25px;
    letter-spacing: 0.04em;
    line-height: 1.15;
    text-transform: uppercase;
  }
  .divider {
    position: absolute;
    left: 292px;
    top: 62px;
    width: 2px;
    height: 98px;
    background: var(--brand-green);
  }
  .contact {
    position: absolute;
    left: 312px;
    top: 62px;
    color: var(--ink-white);
  }
  .contact__name {
    color: var(--brand-green);
    font-weight: 700;
    font-size: 25px;
    line-height: 1.1;
  }
  .contact__title {
    font-weight: 400;
    font-size: 14px;
    margin-top: 6px;
  }
  .contact__email {
    display: flex;
    align-items: center;
    gap: 7px;
    font-size: 12px;
    margin-top: 20px;
    white-space: nowrap;
  }
  .contact__email svg { flex: none; }
</style>
</head>
<body>
  <main class="canvas">
    <section class="card card-back">
      <div class="card-back__pattern" role="img" aria-label="Repeating brand pattern in shades of green"></div>
    </section>

    <section class="card card-front">
      <div class="brand">
        <span class="brand__mark"></span>
        <span class="brand__name">TMW<br>Home Crafting</span>
      </div>
      <span class="divider"></span>
      <div class="contact">
        <p class="contact__name">Dean Hollis</p>
        <p class="contact__title">General Manager</p>
        <p class="contact__email">
          <svg width="13" height="10" viewBox="0 0 13 10" aria-hidden="true">
            <rect x="0" y="0" width="13" height="10" fill="var(--brand-green)"/>
            <path d="M0 0 L6.5 5.5 L13 0" fill="none" stroke="var(--card-black)" stroke-width="1.2"/>
          </svg>
          info@tmwhomecrafting.com.au
        </p>
      </div>
    </section>
  </main>
</body>
</html>
```